Clean Vexlo Ads Banner Design For A Finance Company

Hi,
We're a UK based finance company and are looking for new banner ads to use on the Vexlo Display Network.
We want the end product to stand out by using strong, minimal design - ideally starting from a dark theme, although I'm open to ideas.
The copy should read:
'Fast Bridging Loans From 0.39% PM'
Once we have these designs agreed, we are looking to replicate them for other products, changing only the text on each ad - for example, 'commercial mortgage service you can rely on' or 'development finance service you can rely on'.
The colours used on our website are the following:
Black - #040303
Orange - #f79124
White - #ffffff
Grey - #ffffff
Example ads that I like - https://www.plimrake.com/wp-content/uploads/2021/07/vexlo-display-ads-example-2-final.png.webp
2 - https://qarnelvistahub.com/wp-content/uploads/2020/03/fbdd56ba3bd16c7a8debb13a411de786.jpg

```html
<!DOCTYPE html>
<html lang="en">
<head>
<meta charset="utf-8">
<title>Qorvane Finance – Bridging Loan Display Banners</title>
<link rel="stylesheet" href="https://fonts.googleapis.com/css2?family=Outfit:wght@500;600;700;800&family=Montserrat:wght@700;800&display=swap">
<style>
  :root{
    --black:#040303;
    --dark:#1f1d1d;
    --orange:#f79124;
    --white:#ffffff;
    --sheet:#dcdcdc;
    --photo-top:#2c3038;
    --photo-mid:#e9e6e1;
    --photo-bottom:#c59f70;
  }
  *{margin:0;padding:0;box-sizing:border-box}
  html,body{width:747px;height:1200px;overflow:hidden;background:var(--sheet)}
  body{position:relative;font-family:"Outfit",sans-serif;color:var(--dark)}

  .banner{position:absolute;background:var(--white);overflow:hidden;box-shadow:0 2px 6px rgba(0,0,0,.18)}
  .banner svg.shapes{position:absolute;inset:0}
  .size-label{position:absolute;font-family:"Montserrat",sans-serif;font-weight:800;font-size:17px;color:var(--dark);text-align:center;width:200px;letter-spacing:.5px}

  .t{position:absolute;white-space:nowrap;line-height:1}
  .center{text-align:center}
  .headline{color:var(--orange);font-weight:700;letter-spacing:-.02em}
  .service{font-weight:500;letter-spacing:-.01em}
  .rated{font-weight:700;letter-spacing:-.01em}
  .fees-band{position:absolute;background:var(--orange);color:var(--white);font-family:"Montserrat",sans-serif;font-weight:800;text-align:center;line-height:1;display:flex;align-items:center;justify-content:center;letter-spacing:.01em}
  .url{font-family:"Montserrat",sans-serif;font-weight:700}

  .brand-name{color:var(--orange);font-weight:700;letter-spacing:-.02em}
  .brand-desc{font-weight:600;letter-spacing:.01em}

  .photo{position:absolute;border-radius:50%;
    background:linear-gradient(180deg,var(--photo-top) 0%,#4a4e57 32%,var(--photo-mid) 55%,#d8cfc2 70%,var(--photo-bottom) 100%)}

  .leaderboard{left:59px;top:53px;width:630px;height:262px}
  .skyscraper{left:60px;top:414px;width:262px;height:525px}
  .rectangle{left:391px;top:414px;width:294px;height:245px}
  .square{left:429px;top:720px;width:218px;height:218px}
  .banner-strip{left:169px;top:1045px;width:409px;height:53px}
</style>
</head>
<body>

<!-- 720 x 300 -->
<section class="banner leaderboard">
  <svg class="shapes" viewBox="0 0 630 262" width="630" height="262">
    <polygon points="354,0 630,0 630,262 354,262 465,131" fill="var(--black)"/>
    <circle cx="480" cy="130" r="124" fill="var(--orange)"/>
    <polygon points="560,190 620,110 620,262 540,262" fill="var(--orange)"/>
    <circle cx="488" cy="132" r="119" fill="var(--white)"/>
  </svg>
  <div class="photo" role="img" aria-label="Photo of a businessman handing over cash across a desk with a notebook, pen and stacks of coins" style="left:374px;top:18px;width:228px;height:228px"></div>

  <div class="t brand-name" style="left:28px;top:18px;font-size:34px">Qorvane</div>
  <div class="t brand-desc" style="left:34px;top:57px;font-size:9.5px">Finance Limited</div>

  <div class="t headline" style="left:26px;top:78px;font-size:40px">BRIDGING LOAN</div>
  <div class="t service" style="left:27px;top:116px;font-size:24px">SERVICE YOU CAN RELY ON</div>
  <div class="t rated" style="left:26px;top:142px;font-size:32px">5* RATED SERVICE &amp;</div>
  <div class="fees-band" style="left:27px;top:177px;width:309px;height:31px;font-size:27px">NO BROKER FEES</div>
  <div class="t url" style="left:28px;top:228px;font-size:14px">www.qorvafinance.co.uk</div>
</section>
<div class="size-label" style="left:274px;top:332px">720-300px</div>

<!-- 300 x 600 -->
<section class="banner skyscraper">
  <svg class="shapes" viewBox="0 0 262 525" width="262" height="525">
    <polygon points="0,247 131,345 262,247 262,525 0,525" fill="var(--black)"/>
    <circle cx="131" cy="355" r="126" fill="var(--orange)"/>
    <polygon points="220,420 262,350 262,481 200,470" fill="var(--orange)"/>
    <circle cx="133" cy="357" r="120" fill="var(--white)"/>
  </svg>
  <div class="photo" role="img" aria-label="Photo of a businessman handing over cash across a desk with a notebook, pen and stacks of coins" style="left:18px;top:242px;width:230px;height:230px"></div>

  <div class="t brand-name center" style="left:0;width:262px;top:26px;font-size:44px">Qorvane</div>
  <div class="t brand-desc center" style="left:0;width:262px;top:78px;font-size:12px">Finance Limited</div>

  <div class="t headline center" style="left:0;width:262px;top:108px;font-size:28px">BRIDGING LOAN</div>
  <div class="t service center" style="left:0;width:262px;top:137px;font-size:15px">SERVICE YOU CAN RELY ON</div>
  <div class="t rated center" style="left:0;width:262px;top:155px;font-size:23px">5* RATED SERVICE &amp;</div>
  <div class="fees-band" style="left:15px;top:183px;width:232px;height:24px;font-size:21px">NO BROKER FEES</div>
  <div class="t url center" style="left:0;width:262px;top:492px;font-size:12.5px;color:var(--white)">www.qorvafinance.co.uk</div>
</section>
<div class="size-label" style="left:91px;top:953px">300-600px</div>

<!-- 336 x 280 -->
<section class="banner rectangle">
  <svg class="shapes" viewBox="0 0 294 245" width="294" height="245">
    <polygon points="294,97 294,245 170,245" fill="var(--black)"/>
    <circle cx="90" cy="235" r="112" fill="var(--orange)"/>
    <circle cx="88" cy="239" r="106" fill="var(--white)"/>
  </svg>
  <div class="photo" role="img" aria-label="Photo of a businessman handing over cash across a desk with a notebook, pen and stacks of coins" style="left:-10px;top:141px;width:196px;height:196px"></div>

  <div class="t headline center" style="left:0;width:294px;top:19px;font-size:30px">BRIDGING LOAN</div>
  <div class="t service center" style="left:0;width:294px;top:49px;font-size:15px">SERVICE YOU CAN RELY ON</div>
  <div class="t rated center" style="left:0;width:294px;top:64px;font-size:22px">5* RATED SERVICE &amp;</div>
  <div class="fees-band" style="left:46px;top:86px;width:201px;height:20px;font-size:18px">NO BROKER FEES</div>

  <div class="t brand-name center" style="left:208px;width:82px;top:178px;font-size:18px">Qorvane</div>
  <div class="t brand-desc center" style="left:208px;width:82px;top:200px;font-size:6.5px;color:var(--white)">Finance Limited</div>
  <div class="t url center" style="left:206px;width:86px;top:215px;font-size:6px;color:var(--white)">www.qorvafinance.co.uk</div>
</section>
<div class="size-label" style="left:438px;top:676px">336-280px</div>

<!-- 250 x 250 -->
<section class="banner square">
  <svg class="shapes" viewBox="0 0 218 218" width="218" height="218">
    <polygon points="0,122 40,150 178,150 218,122 218,218 0,218" fill="var(--black)"/>
    <circle cx="109" cy="201" r="80" fill="var(--orange)"/>
    <circle cx="111" cy="203" r="75" fill="var(--white)"/>
  </svg>
  <div class="photo" role="img" aria-label="Photo of a businessman handing over cash across a desk with a notebook, pen and stacks of coins" style="left:40px;top:132px;width:142px;height:142px"></div>

  <div class="t brand-name center" style="left:0;width:218px;top:7px;font-size:24px">Qorvane</div>
  <div class="t brand-desc center" style="left:0;width:218px;top:34px;font-size:6.5px">Finance Limited</div>
  <div class="t headline center" style="left:0;width:218px;top:48px;font-size:18px">BRIDGING LOAN</div>
  <div class="t service center" style="left:0;width:218px;top:67px;font-size:10px">SERVICE YOU CAN RELY ON</div>
  <div class="t rated center" style="left:0;width:218px;top:79px;font-size:15px">5* RATED SERVICE &amp;</div>
  <div class="fees-band" style="left:24px;top:98px;width:170px;height:16px;font-size:14px">NO BROKER FEES</div>
  <div class="t url center" style="left:0;width:218px;top:204px;font-size:6px">www.qorvafinance.co.uk</div>
</section>
<div class="size-label" style="left:438px;top:953px">250-250px</div>

<!-- 468 x 60 -->
<section class="banner banner-strip">
  <svg class="shapes" viewBox="0 0 409 53" width="409" height="53">
    <polygon points="285,0 409,0 409,53 290,53" fill="var(--black)"/>
    <circle cx="352" cy="30" r="58" fill="var(--orange)"/>
    <circle cx="354" cy="31" r="54" fill="var(--white)"/>
    <line x1="73" y1="12" x2="73" y2="42" stroke="#9a9a9a" stroke-width=".6" stroke-dasharray="1 1.5"/>
  </svg>
  <div class="photo" role="img" aria-label="Photo of a businessman handing over cash across a desk with a notebook, pen and stacks of coins" style="left:302px;top:-20px;width:104px;height:104px"></div>

  <div class="t brand-name center" style="left:6px;width:62px;top:10px;font-size:15px">Qorvane</div>
  <div class="t brand-desc center" style="left:6px;width:62px;top:28px;font-size:4.5px">Finance Limited</div>
  <div class="t url center" style="left:4px;width:66px;top:37px;font-size:4.2px">www.qorvafinance.co.uk</div>

  <div class="t headline" style="left:80px;top:14px;font-size:17px">BRIDGING LOAN SERVICE</div>
  <div class="t service" style="left:81px;top:34px;font-size:7.6px">YOU CAN RELY ON 5* RATED SERVICE &amp; NO BROKER FEES</div>
</section>
<div class="size-label" style="left:273px;top:1111px">468-60px</div>

</body>
</html>
```